Logo, Web and Mobile Designs for enterprise social media platform

All the details are in the attached document, please start reading the scope document first which explains what is this project about and the details about the needed deliverables, after that please read the UI_Requirements document which will detail what is expected regarding the coded web version since this is a coded contest, it is very important that you meet the UI requirements or suggest something else but we will need to agree first before working on the coded version

Good Luck

Target Market(s)

Enterprise Social Media

Industry/Entity Type

Media

Coding

Coded - Design and coding required

Number of Pages Required

5+ page

Font styles to use
Sans Serif

Requirements
Must have
• All the must haves are listed in the scope document so please check before you start

```html
<!DOCTYPE html>
<html lang="en">
<head>
<meta charset="utf-8">
<title>Teamora – Create New Business Opportunity</title>
<link rel="stylesheet" href="https://fonts.googleapis.com/css2?family=Open+Sans:wght@400;600;700&display=swap">
<style>
  :root{
    --page:#ffffff;
    --header-top:#ffffff;
    --header-bottom:#f3f3f3;
    --rule:#e3e3e3;
    --icon:#6b6b6b;
    --brand-blue:#2a9fd6;
    --brand-orange:#f39c12;
    --text:#555555;
    --text-dark:#444444;
    --panel-head-text:#5a6270;
    --panel-head:#f6f7f9;
    --field-border:#e2e2e2;
    --btn-blue-top:#33b2e2;
    --btn-blue-bottom:#2499c9;
    --btn-orange:#e8920b;
    --btn-orange-shadow:#c27506;
    --footer:#1e8cb8;
    --white:#ffffff;
  }
  *{box-sizing:border-box;margin:0;padding:0}
  html,body{width:1200px;height:2445px;overflow:hidden;background:var(--page);
    font-family:"Open Sans",Arial,sans-serif;color:var(--text)}
  .canvas{position:relative;width:1200px;height:2445px}

  .site-header{position:absolute;left:0;top:0;width:1200px;height:233px;
    background:linear-gradient(var(--header-top),var(--header-bottom));
    border-bottom:4px solid var(--rule)}
  .site-header .divider{position:absolute;top:0;width:2px;height:229px;background:var(--rule)}
  .home-btn{position:absolute;left:77px;top:94px}
  .menu-btn{position:absolute;left:1072px;top:97px}
  .brand{position:absolute;left:348px;top:72px;display:flex;align-items:center;gap:22px}
  .brand-dot{width:92px;height:92px;border-radius:50%;background:var(--brand-orange)}
  .brand-name{font-size:74px;font-weight:600;color:var(--brand-blue);letter-spacing:1px}

  .panel{position:absolute;left:43px;top:311px;width:1115px;height:1676px;
    border:3px solid var(--rule);background:var(--white)}
  .panel-head{height:143px;background:var(--panel-head);border-bottom:3px solid var(--rule);
    padding-left:40px;display:flex;align-items:center;font-size:35px;color:var(--panel-head-text)}

  .label{position:absolute;font-size:39px;color:var(--text)}
  .field{position:absolute;height:113px;border:3px solid var(--field-border);border-radius:6px;background:var(--white)}
  .upload-row{position:absolute;left:103px;width:994px;height:113px;display:flex}
  .upload-row .field{position:static;flex:1;border-radius:6px 0 0 6px}
  .upload-btn{width:391px;height:113px;border-radius:0 6px 6px 0;
    background:linear-gradient(var(--btn-blue-top),var(--btn-blue-bottom));
    color:var(--white);font-size:38px;display:flex;align-items:center;justify-content:center;letter-spacing:1px}

  .file-item{position:absolute;left:103px;top:995px;display:flex;align-items:center;gap:24px;font-size:35px;color:var(--text-dark)}

  .date-field{left:433px;width:520px;font-size:30px;color:var(--text-dark);display:flex;align-items:center;padding-left:50px}
  .time-field{left:433px;width:518px;display:flex;padding:0}
  .time-field .hm{width:294px;display:flex;align-items:center;justify-content:center;gap:38px;font-size:40px;color:var(--text-dark);border-right:3px solid var(--field-border)}
  .time-field .spin{width:100px;display:flex;align-items:center;justify-content:center;border-right:3px solid var(--field-border)}
  .time-field .ampm{flex:1;display:flex;align-items:center;justify-content:center;font-size:38px;color:var(--text-dark)}

  .save-btn{position:absolute;left:113px;top:1804px;width:684px;height:105px;border-radius:8px;
    background:var(--btn-orange);box-shadow:0 7px 0 var(--btn-orange-shadow);
    color:var(--white);font-size:42px;font-weight:700;display:flex;align-items:center;justify-content:center}

  .site-footer{position:absolute;left:0;top:2077px;width:1200px;height:368px;background:var(--footer);color:var(--white);text-align:center}
  .social{position:absolute;top:78px;left:0;width:1200px;display:flex;justify-content:center;gap:28px}
  .social span{width:58px;height:58px;border-radius:10px;background:var(--white)}
  .footer-nav{position:absolute;top:172px;left:0;width:1200px;font-size:35px;word-spacing:2px}
  .footer-nav .sep{margin:0 22px}
  .copyright{position:absolute;top:253px;left:0;width:1200px;font-size:35px}
</style>
</head>
<body>
<div class="canvas">
  <header class="site-header">
    <svg class="home-btn" width="50" height="46" viewBox="0 0 50 46" aria-label="Home">
      <path d="M25 3 L2 24 L8 24 L8 44 L20 44 L20 31 L30 31 L30 44 L42 44 L42 24 L48 24 Z" fill="var(--icon)"/>
    </svg>
    <div class="divider" style="left:214px"></div>
    <div class="brand"><span class="brand-dot"></span><span class="brand-name">Teamora</span></div>
    <div class="divider" style="left:991px"></div>
    <svg class="menu-btn" width="50" height="42" viewBox="0 0 50 42" aria-label="Menu">
      <rect x="0" y="0" width="50" height="8" rx="2" fill="var(--icon)"/>
      <rect x="0" y="17" width="50" height="8" rx="2" fill="var(--icon)"/>
      <rect x="0" y="34" width="50" height="8" rx="2" fill="var(--icon)"/>
    </svg>
  </header>

  <main class="panel">
    <div class="panel-head">CREATE NEW BUSINESS OPPORTUNITY - STEP 2</div>
  </main>

  <div class="label" style="left:103px;top:520px">Upload Banner Photo : *</div>
  <div class="upload-row" style="top:601px"><div class="field"></div><div class="upload-btn">UPLOADED</div></div>

  <div class="label" style="left:103px;top:754px">Upload Files : *</div>
  <div class="upload-row" style="top:836px"><div class="field"></div><div class="upload-btn">UPLOADED</div></div>

  <div class="file-item">
    <svg width="50" height="40" viewBox="0 0 50 40" aria-hidden="true">
      <rect x="2" y="2" width="46" height="36" fill="none" stroke="var(--icon)" stroke-width="4"/>
      <circle cx="14" cy="13" r="4" fill="var(--icon)"/>
      <path d="M6 34 L18 22 L25 28 L35 16 L44 34 Z" fill="var(--icon)"/>
    </svg>
    <span>partner-logo.png</span>
  </div>

  <div class="label" style="left:103px;top:1127px">From Date :</div>
  <div class="field date-field" style="top:1097px">12 - 10 - 2015</div>

  <div class="label" style="left:103px;top:1302px">To Date :</div>
  <div class="field date-field" style="top:1275px">12 - 10 - 2015</div>

  <div class="label" style="left:106px;top:1468px">From Time :</div>
  <div class="field time-field" style="top:1440px">
    <div class="hm"><span>10</span><span>:</span><span>48</span></div>
    <div class="spin"><svg width="30" height="54" viewBox="0 0 30 54" aria-hidden="true"><path d="M4 18 L15 7 L26 18 M4 36 L15 47 L26 36" fill="none" stroke="var(--icon)" stroke-width="3.5"/></svg></div>
    <div class="ampm">AM</div>
  </div>

  <div class="label" style="left:103px;top:1645px">To Time :</div>
  <div class="field time-field" style="top:1618px">
    <div class="hm"><span>10</span><span>:</span><span>48</span></div>
    <div class="spin"><svg width="30" height="54" viewBox="0 0 30 54" aria-hidden="true"><path d="M4 18 L15 7 L26 18 M4 36 L15 47 L26 36" fill="none" stroke="var(--icon)" stroke-width="3.5"/></svg></div>
    <div class="ampm">AM</div>
  </div>

  <div class="save-btn">SAVE AND GO TO STEP 2</div>

  <footer class="site-footer">
    <div class="social"><span></span><span></span><span></span><span></span><span></span></div>
    <nav class="footer-nav">Home<span class="sep">/</span>Contact<span class="sep">/</span>Topics<span class="sep">/</span>Posts &amp; Comments<span class="sep">/</span>Videos Links</nav>
    <div class="copyright">Copyright @ 2015 - 2015.Teamora. All Rights Reserved.</div>
  </footer>
</div>
</body>
</html>
```